Business card (AI file uploaded)

We need a business card design that is minimalist using existing logo (attached). Source files must be editable so we can make the same design with other names.

Screenshots included of a design I was working on to give you an idea of the style I would like. Looking for similar modern styles

Thanks

```html
<!DOCTYPE html>
<html lang="en">
<head>
<meta charset="utf-8">
<title>Marlow Law Group – Business Card Proof</title>
<link href="https://fonts.googleapis.com/css2?family=Open+Sans:wght@400;500&display=swap" rel="stylesheet">
<style>
  :root {
    --paper: #ffffff;
    --ink: #111111;
    --label-red: #e5202a;
    --bleed-line: #e14ad6;
    --trim-line: #4a4a4a;
    --safe-line: #5fe0cf;
    --crop-mark: #8a8a8a;
  }
  html, body {
    margin: 0;
    padding: 0;
    width: 928px;
    height: 1200px;
    overflow: hidden;
    background: var(--paper);
  }
  .proof-sheet {
    display: block;
    width: 928px;
    height: 1200px;
    font-family: "Open Sans", Arial, sans-serif;
  }
  .side-label { fill: var(--label-red); font-size: 29px; }
  .bleed { fill: none; stroke: var(--bleed-line); stroke-width: 1.3; }
  .trim { fill: none; stroke: var(--trim-line); stroke-width: 2.2; }
  .safe { fill: none; stroke: var(--safe-line); stroke-width: 1.3; }
  .crop-mark { stroke: var(--crop-mark); stroke-width: 1.3; }
  .firm-name { fill: var(--ink); font-size: 31px; font-weight: 400; letter-spacing: -0.5px; }
  .firm-sub { fill: var(--ink); font-size: 14px; font-weight: 400; letter-spacing: 3.2px; }
  .firm-mark { fill: var(--ink); }
  .person-name { fill: var(--ink); font-size: 25px; font-weight: 400; }
  .person-title, .practice-areas, .contact-line { fill: var(--ink); font-size: 13px; font-weight: 400; }
</style>
</head>
<body>
<svg class="proof-sheet" viewBox="0 0 928 1200" xmlns="http://www.w3.org/2000/svg">

  <!-- Front side -->
  <g class="card-front">
    <text class="side-label" x="259" y="160">front</text>

    <line class="crop-mark" x1="270" y1="235" x2="270" y2="261"/>
    <line class="crop-mark" x1="653" y1="235" x2="653" y2="261"/>
    <line class="crop-mark" x1="270" y1="534" x2="270" y2="563"/>
    <line class="crop-mark" x1="653" y1="534" x2="653" y2="563"/>
    <line class="crop-mark" x1="205" y1="288" x2="241" y2="288"/>
    <line class="crop-mark" x1="683" y1="288" x2="719" y2="288"/>
    <line class="crop-mark" x1="205" y1="507" x2="241" y2="507"/>
    <line class="crop-mark" x1="683" y1="507" x2="719" y2="507"/>

    <rect class="bleed" x="258" y="275" width="409" height="246"/>
    <rect class="trim" x="271" y="288" width="382" height="219"/>
    <rect class="safe" x="284" y="301" width="356" height="192"/>

    <text class="firm-name" x="288" y="336">MARLOW</text>
    <text class="firm-sub" x="289" y="353">LAW GROUP</text>
    <circle class="firm-mark" cx="599" cy="340" r="31"/>

    <text class="person-name" x="464" y="420" text-anchor="middle">Evan Marlow</text>
    <text class="person-title" x="464" y="439" text-anchor="middle">Attorney At Law</text>
    <text class="practice-areas" x="462" y="471" text-anchor="middle">Real Estate  |  Bankruptcy  |  Social Security Disability</text>
  </g>

  <!-- Back side -->
  <g class="card-back">
    <text class="side-label" x="270" y="655">back</text>

    <line class="crop-mark" x1="270" y1="705" x2="270" y2="734"/>
    <line class="crop-mark" x1="653" y1="705" x2="653" y2="734"/>
    <line class="crop-mark" x1="270" y1="1003" x2="270" y2="1036"/>
    <line class="crop-mark" x1="653" y1="1003" x2="653" y2="1036"/>
    <line class="crop-mark" x1="205" y1="760" x2="241" y2="760"/>
    <line class="crop-mark" x1="683" y1="760" x2="719" y2="760"/>
    <line class="crop-mark" x1="205" y1="979" x2="241" y2="979"/>
    <line class="crop-mark" x1="683" y1="979" x2="719" y2="979"/>

    <rect class="bleed" x="258" y="747" width="409" height="245"/>
    <rect class="trim" x="271" y="760" width="382" height="219"/>
    <rect class="safe" x="284" y="773" width="356" height="193"/>

    <text class="contact-line" x="463" y="848" text-anchor="middle">410 Lakeview Ave., Suite 200, Brookfield, IL 60513</text>
    <text class="contact-line" x="463" y="873" text-anchor="middle">P: 630.555.0142      F: 630.555.0187</text>
    <text class="contact-line" x="463" y="899" text-anchor="middle">marlow@marlowlaw.com</text>
  </g>
</svg>
</body>
</html>
```